Web Design Project

Desisgn a new style for the proposed website as per the attached link. The logo will remain as is, and it is likely that the colours will be as per the attached style guide.

Otherwise look and feel, icons, layout, images are within scope.

Current prosposed home page:
http://vantrelux-newsite.pagemorrowhost.com/index

Target Market(s)

Typically, large organisations from any industry such as Airlines, banks, Govt agencies.

Could be operational executives, business improvement specialists, bsuienss analysts.

```html
<!DOCTYPE html>
<html lang="en">
<head>
<meta charset="utf-8">
<title>Vantrelux – Home</title>
<link href="https://fonts.googleapis.com/css2?family=Open+Sans:wght@300;400;600;700&display=swap" rel="stylesheet">
<style>
:root{
  --blue:#1e74b8;
  --blue-light:#3b95d6;
  --nav:#2f6fa6;
  --ink:#3a3f45;
  --muted:#6b7178;
  --page:#e7eaed;
  --panel:#ffffff;
  --line:#d3d8dd;
  --footer:#26303a;
  --footer-text:#9aa4ae;
  --red:#c0392b;
}
*{box-sizing:border-box;margin:0;padding:0}
html,body{width:900px;height:1200px;overflow:hidden}
body{background:var(--page);font-family:"Open Sans",Arial,sans-serif;color:var(--ink);position:relative}
.site{position:absolute;left:30px;top:0;width:840px;height:1200px;background:var(--panel)}
.header{position:absolute;left:0;top:0;width:840px;height:66px;background:#f6f7f8;border-bottom:1px solid var(--line)}
.brand{position:absolute;left:16px;top:14px;font-size:21px;font-weight:600;color:var(--ink)}
.contact-strip{position:absolute;right:16px;top:8px;display:flex;align-items:center;gap:5px;font-size:11px;color:var(--muted)}
.social{width:16px;height:16px;border-radius:3px;background:var(--blue-light)}
.social.alt{background:#5a6d80}
.nav{position:absolute;right:12px;top:38px;display:flex;gap:2px}
.nav a{display:block;padding:6px 9px;background:var(--nav);color:#fff;font-size:10px;font-weight:600;text-decoration:none;letter-spacing:.3px}
.hero{position:absolute;left:0;top:70px;width:840px;height:188px;background:linear-gradient(180deg,#f4f5f6,#d9dde1)}
.hero-title{position:absolute;left:300px;top:40px;font-size:22px;font-weight:300;color:#333;line-height:1.25}
.hero-arrow{position:absolute;top:76px;width:22px;height:36px}
.intro-title{position:absolute;left:16px;top:286px;font-size:27px;font-weight:300;color:var(--blue)}
.intro-rule{position:absolute;left:16px;top:328px;width:808px;height:1px;background:var(--line)}
.intro-text{position:absolute;left:16px;top:342px;width:530px;font-size:11.5px;line-height:1.6;color:var(--ink)}
.intro-text p{margin-bottom:12px}
.news{position:absolute;left:570px;top:342px;width:254px;height:330px;border:1px solid var(--line);background:#fafbfc;padding:10px}
.news h3{font-size:14px;font-weight:600;color:#555;border-bottom:1px solid var(--line);padding-bottom:6px;margin-bottom:8px}
.news h3 span{color:var(--red)}
.news-item{display:flex;gap:8px;margin-bottom:10px}
.date{width:40px;flex:none;background:var(--blue);color:#fff;text-align:center;font-size:9px;line-height:1.2;padding:4px 0}
.date b{display:block;font-size:14px}
.date.red{background:var(--red)}
.news-item p{font-size:9.5px;line-height:1.35;color:var(--muted)}
.news-item p strong{color:var(--ink)}
.capabilities{position:absolute;left:16px;top:760px;width:808px;display:flex;gap:8px}
.cap{flex:1;height:50px;border:1px solid var(--line);background:linear-gradient(#fff,#eef1f4);display:flex;align-items:center;gap:7px;padding:0 7px;font-size:10px;line-height:1.2;color:var(--ink)}
.cap svg{flex:none}
.feature{position:absolute;left:16px;top:836px;width:808px;height:170px;border-top:1px solid var(--line);padding-top:14px}
.video{position:absolute;left:0;top:14px;width:200px;height:140px;background:linear-gradient(135deg,#3f5263,#1b242d)}
.video-label{position:absolute;left:10px;bottom:14px;color:#fff;font-size:15px;font-weight:700;line-height:1.1}
.play{position:absolute;left:82px;top:46px}
.feature-text{position:absolute;left:222px;top:14px;width:320px;font-size:11.5px;line-height:1.5}
.feature-text p{margin-bottom:12px}
.feature-text a{color:var(--blue);font-size:11px}
.btn{position:absolute;left:580px;width:228px;height:42px;background:linear-gradient(#5aa8e0,#2f7fc0);color:#fff;font-size:14px;display:flex;align-items:center;justify-content:center;border-radius:3px}
.footer{position:absolute;left:0;top:1016px;width:840px;height:184px;background:var(--footer);padding:16px}
.footer-col{position:absolute;top:16px;font-size:9.5px;line-height:1.55;color:var(--footer-text)}
.footer-col h4{font-size:11px;color:var(--blue-light);font-weight:700;margin-bottom:4px;letter-spacing:.3px}
.footer-col .sub-head{color:var(--blue-light);font-weight:700}
.copyright{position:absolute;right:20px;top:22px;text-align:right;font-size:10px;color:var(--footer-text);line-height:1.5}
</style>
</head>
<body>
<div class="site">
  <header class="header">
    <div class="brand">Vantrelux</div>
    <div class="contact-strip">Get in Touch <span class="social"></span><span class="social alt"></span><span class="social"></span></div>
    <nav class="nav">
      <a>PRODUCTS</a><a>SERVICES</a><a>SOLUTIONS</a><a>RESOURCES</a><a>CUSTOMER STORIES</a><a>ABOUT US</a><a>CONTACT</a>
    </nav>
  </header>

  <section class="hero" role="img" aria-label="Banner image of a crowd of grey business figures around a central highlighted figure">
    <div class="hero-title">We power and de-risk business<br>transformations</div>
    <svg class="hero-arrow" style="left:6px" viewBox="0 0 22 36"><path d="M16 4 L5 18 L16 32" fill="none" stroke="#555" stroke-width="4"/></svg>
    <svg class="hero-arrow" style="right:6px" viewBox="0 0 22 36"><path d="M6 4 L17 18 L6 32" fill="none" stroke="#555" stroke-width="4"/></svg>
  </section>

  <h1 class="intro-title">We power and de-risk business transformations</h1>
  <div class="intro-rule"></div>
  <div class="intro-text">
    <p>Operational excellence and business transformation is achieved by understanding and capturing every detail of your business. High performing companies have a single view of the complex relationships between systems, processes and people supported by in-depth organisational knowledge. Vantrelux's Operational Business Management System (OBMS) empowers and de-risks large transformation initiatives enabling continuous improvement for high performing organisations.</p>
    <p>An OBMS captures the DNA of your business. It links people, processes and systems in a way that visualises how your organisation works today, and how it may change in the future. This information is managed in a re-usable and extendable framework and is distributed to the many stakeholders in a form that meets their individual needs.</p>
    <p>This unique way of reaching, engaging and empowering everyone involved in your business allows you to continually excel in your operations and reduce costs while maintaining compliance and governance standards. Vantrelux's OBMS allows you to:</p>
  </div>

  <aside class="news">
    <h3>News &amp; <span>Events</span></h3>
    <div class="news-item"><div class="date red"><b>12</b>FEB</div><p><strong>Lorem ipsum dolor sit amet,</strong> consectetur adipiscing elit, sed do eiusmod tempor incididunt ut labore.</p></div>
    <div class="news-item"><div class="date"><b>08</b>FEB</div><p><strong>Lorem ipsum dolor sit amet,</strong> consectetur adipiscing elit, sed do eiusmod tempor incididunt ut labore.</p></div>
    <div class="news-item"><div class="date"><b>30</b>JAN</div><p><strong>Lorem ipsum dolor</strong> consectetur adipiscing elit, sed do eiusmod tempor incididunt ut labore.</p></div>
    <div class="news-item"><div class="date"><b>21</b>JAN</div><p><strong>Lorem ipsum dolor sit amet,</strong> consectetur adipiscing elit, sed do eiusmod tempor incididunt ut labore.</p></div>
    <div class="news-item"><div class="date"><b>15</b>JAN</div><p><strong>Lorem ipsum dolor sit amet,</strong> consectetur adipiscing elit, sed do eiusmod tempor incididunt ut labore.</p></div>
  </aside>

  <div class="capabilities">
    <div class="cap"><svg width="26" height="26" viewBox="0 0 26 26"><circle cx="13" cy="13" r="12" fill="#e8f1f9" stroke="#1e74b8" stroke-width="2"/><circle cx="13" cy="13" r="4" fill="#1e74b8"/></svg>Knowledge Management</div>
    <div class="cap"><svg width="26" height="26" viewBox="0 0 26 26"><path d="M4 18 L10 12 L15 16 L22 7" fill="none" stroke="#2a9d5a" stroke-width="3"/></svg>Continuous Improvement</div>
    <div class="cap"><svg width="26" height="26" viewBox="0 0 26 26"><path d="M4 13 H20 M14 7 L20 13 L14 19" fill="none" stroke="#1e74b8" stroke-width="3"/></svg>Business Transformation</div>
    <div class="cap"><svg width="26" height="26" viewBox="0 0 26 26"><rect x="4" y="6" width="18" height="13" fill="none" stroke="#555" stroke-width="2"/><rect x="9" y="20" width="8" height="2" fill="#555"/></svg>System Requirements</div>
    <div class="cap"><svg width="26" height="26" viewBox="0 0 26 26"><rect x="2" y="4" width="8" height="7" fill="#e67e22"/><rect x="16" y="15" width="8" height="7" fill="#e67e22"/><path d="M6 11 V18 H16" fill="none" stroke="#555" stroke-width="2"/></svg>Business Process Modelling</div>
    <div class="cap"><svg width="26" height="26" viewBox="0 0 26 26"><path d="M5 13 L11 19 L21 7" fill="none" stroke="#1e74b8" stroke-width="3"/></svg>Governance &amp; Compliance</div>
  </div>

  <section class="feature">
    <div class="video" role="img" aria-label="Video thumbnail introducing the operational business management system">
      <svg class="play" width="36" height="36" viewBox="0 0 36 36"><circle cx="18" cy="18" r="17" fill="rgba(255,255,255,.25)"/><path d="M14 10 L26 18 L14 26Z" fill="#fff"/></svg>
      <div class="video-label">VIDEO TO COME<br>FOR YOUR SITE</div>
    </div>
    <div class="feature-text">
      <p>"Vantrelux's Operational Business Management System (OBMS) addresses the key challenge of understanding organic knowledge and creating organisational knowledge.</p>
      <a>Click for more...</a>
    </div>
    <div class="btn" style="top:28px">View A Sample Model</div>
    <div class="btn" style="top:84px">Contact Information</div>
  </section>

  <footer class="footer">
    <div class="footer-col" style="left:16px"><h4>PRODUCTS</h4>Model Library<br>Vantrelux Modeller<br>- Desktop Modelling Suite<br>- Process Modeller Add-on<br>- Enterprise Publisher<br>- Corporate Governance Module</div>
    <div class="footer-col" style="left:200px"><h4>SERVICES</h4>Coaching &amp; Mentoring<br>Technical Services<br><span class="sub-head">NEWS &amp; EVENTS</span><br>Announcements<br>Technical Notes</div>
    <div class="footer-col" style="left:370px"><h4>TRAINING &amp; SUPPORT</h4>Web-Based Tutorials<br>Course Calendar<br>Knowledge Base<br>Support<br>Training Courses</div>
    <div class="copyright">© All Rights Reserved 2013<br>Vantrelux</div>
  </footer>
</div>
</body>
</html>
```